OpenHarbor Yoga Website Design

Business Logo - attached
5 pages being:
Home
About
Classes
Blog
Contact

Would like Scrolling webpage and yoga symbols to be used.

Must have's being:
Easy to navigate, Text needs to be able to be edited/updated, Enquire Now Links, More Information Links, be a secure site, SEO,

Please refer to attached document for the information for the body of the website.

Target Market(s)

Educators, Community Service, Health and Wellbeing, Mental Health

Industry/Entity Type

Yoga

Coding

Coded - Design and coding required

Number of Pages Required

5+ page

Font styles to use
Other font styles liked:
• Bella Bold BC

Colors
0094D4
00A9DD
6FCCEA
C7EBF8
E9F6FB
6B429C
8869AF
B7A5CE
E3DAEB
F3F0F8

Requirements
Must have
• Easy to navigate, Text needs to be able to be edited/updated, Enquire Now Links, More Information Links, be a secure site, SEO,
Nice to have
• Scrolling webpage, yoga symbols

```html
<!DOCTYPE html>
<html lang="en">
<head>
<meta charset="utf-8">
<title>OpenHarbor Yoga</title>
<link rel="stylesheet" href="https://fonts.googleapis.com/css2?family=Cormorant+Garamond:wght@500;600;700&family=Kaushan+Script&family=Lato:wght@400;700&display=swap">
<style>
:root{
  --purple:#6b2fc9;
  --plum:#6b2f8c;
  --deep:#5a2d91;
  --cyan:#2bd3e8;
  --lilac:#b7a5ce;
  --ink:#222;
  --dark:#161616;
  --white:#fff;
}
*{box-sizing:border-box;margin:0;padding:0}
html,body{width:1200px;height:2753px;overflow:hidden;background:var(--white)}
body{position:relative;font-family:"Lato",sans-serif;color:var(--ink)}
.abs{position:absolute}
.script{font-family:"Kaushan Script",cursive}

/* hero */
.hero-photo{left:0;top:0;width:1200px;height:700px;background:linear-gradient(180deg,#f3d9bd 0%,#c79a76 35%,#8e6a55 60%,#b79b8b 100%)}
.hero-waves{left:0;top:0}
.brand-tab{left:111px;top:0;width:162px;height:170px;background:var(--white);border-radius:0 0 70px 70px;display:flex;align-items:center;justify-content:center;text-align:center}
.brand-tab span{font-family:"Cormorant Garamond",serif;font-weight:700;color:var(--purple);font-size:22px;line-height:1.1}
.nav{top:30px;left:437px;display:flex;gap:45px;font-family:"Cormorant Garamond",serif;font-weight:600;font-size:20px;color:#1d1d1d}
.quote-btn{left:911px;top:18px;width:177px;height:51px;background:var(--purple);color:var(--white);border-radius:10px;font-family:"Cormorant Garamond",serif;font-weight:700;font-size:19px;display:flex;align-items:center;justify-content:center}
.hero-pre{left:110px;top:226px;color:var(--white);font-size:26px;letter-spacing:3px}
.hero-title{left:108px;top:268px;color:var(--white);font-size:78px;font-weight:400;white-space:nowrap;text-shadow:0 3px 6px rgba(0,0,0,.25)}
.pill{background:var(--white);border-radius:12px 26px 12px 26px;box-shadow:0 4px 10px rgba(0,0,0,.2);display:flex;align-items:center;justify-content:center;font-family:"Cormorant Garamond",serif;font-weight:700;font-size:23px;color:var(--plum)}
.get-started{left:111px;top:396px;width:173px;height:55px}
.arrow{width:32px;height:32px;border-radius:50%;background:var(--white);display:flex;align-items:center;justify-content:center}

/* about */
.about-band{left:0;top:600px;width:1200px;height:622px;background:linear-gradient(180deg,#5d2f92 0%,#4c5aa8 40%,#2a9fd0 72%,#2bd3e8 100%)}
.about-photo{left:112px;top:771px;width:411px;height:529px;border:5px solid var(--white);border-radius:0 0 150px 0;background:linear-gradient(180deg,#e6e4e2,#d3cfcb 60%,#bdb7b3);box-shadow:0 6px 16px rgba(0,0,0,.2)}
.about-mark{left:602px;top:768px;width:48px;height:48px;border:2px solid var(--white);border-radius:50%}
.about-title{left:600px;top:826px;color:var(--white);font-size:40px;font-weight:400;white-space:nowrap}
.about-text{left:600px;top:891px;width:500px;color:var(--white);font-size:15px;line-height:31px}
.about-text p+p{margin-top:31px}
.read-more{left:600px;top:1121px;width:165px;height:55px}

/* benefits */
.benefits-mark{left:576px;top:1335px;width:48px;height:48px;border:2px solid var(--lilac);border-radius:50%}
.benefits-title{left:0;width:1200px;top:1385px;text-align:center;color:var(--plum);font-size:40px;font-weight:400}
.benefits-intro{left:180px;width:840px;top:1451px;text-align:center;font-size:15px;line-height:29px}
.col-title{font-family:"Cormorant Garamond",serif;font-weight:600;font-size:30px;line-height:36px;color:var(--purple);white-space:nowrap}
.col-list{font-size:13.5px;line-height:26.5px;list-style:none}
.col-list b{font-weight:700}
.bodies{left:110px;top:1546px;width:180px}
.minds{left:908px;top:1546px;width:185px}
.spirits{left:400px;top:2116px;width:400px;text-align:center}
.icon-disc{width:118px;height:118px;border-radius:50%;background:var(--deep)}
.centre-mark{left:470px;top:1640px;width:260px;height:260px;border-radius:50%;background:radial-gradient(circle,#d9c8f7 0%,#ae8cf0 50%,rgba(174,140,240,0) 72%)}

/* footer */
.footer{left:0;top:2365px;width:1200px;height:326px;background:radial-gradient(circle at 220px 150px,#2c2c2c,var(--dark) 60%)}
.foot-brand{left:112px;top:2430px;width:140px;text-align:center;font-family:"Cormorant Garamond",serif;font-weight:700;font-size:24px;line-height:1.1;color:var(--white)}
.social{width:32px;height:32px;border-radius:50%;background:var(--white)}
.foot-head{color:var(--white);font-size:24px;font-weight:400}
.foot-list{list-style:none;color:var(--white);font-size:16px}
.foot-list li{height:34.4px;display:flex;align-items:center;gap:10px}
.contact-row{display:flex;gap:12px;align-items:center;color:var(--white);font-size:16px;line-height:27px}
.ico{width:33px;height:33px;border-radius:50%;background:var(--white);display:flex;align-items:center;justify-content:center;flex:none}
.copyright{left:0;top:2691px;width:1200px;height:62px;background:linear-gradient(180deg,#6b2fc9,#4a7be0 70%,#2bd3e8);color:var(--white);font-weight:700;font-size:16px;display:flex;align-items:center;justify-content:center}
</style>
</head>
<body>

<!-- hero -->
<div class="abs hero-photo" role="img" aria-label="Woman meditating in lotus pose by a misty mountain lake at sunrise"></div>
<svg class="abs hero-waves" width="1200" height="720" viewBox="0 0 1200 720">
  <path d="M0 520 C200 470 330 560 520 540 C700 520 850 470 1200 520 L1200 720 L0 720Z" fill="rgba(255,255,255,.35)"/>
  <path d="M0 560 C180 520 300 620 480 600 C650 580 800 500 1200 560 L1200 720 L0 720Z" fill="rgba(255,255,255,.5)"/>
  <path d="M0 630 C120 610 250 700 400 700 C560 700 620 600 760 610 C900 620 1000 580 1200 600 L1200 720 L0 720Z" fill="#5d2f92"/>
</svg>
<div class="abs brand-tab"><span>OpenHarbor<br>Yoga</span></div>
<nav class="abs nav"><span>Home</span><span>About</span><span>Classes</span><span>Blog</span><span>Contact</span></nav>
<div class="abs quote-btn">Request A Quote</div>
<div class="abs hero-pre script">Welcome to</div>
<h1 class="abs hero-title script">OpenHarbor Yoga</h1>
<div class="abs pill get-started">Get Started</div>
<div class="abs arrow" style="left:31px;top:283px"><svg width="14" height="14" viewBox="0 0 14 14"><path d="M9 2 L4 7 L9 12" fill="none" stroke="#222" stroke-width="2.5"/></svg></div>
<div class="abs arrow" style="left:1125px;top:283px"><svg width="14" height="14" viewBox="0 0 14 14"><path d="M5 2 L10 7 L5 12" fill="none" stroke="#222" stroke-width="2.5"/></svg></div>

<!-- about -->
<div class="abs about-band" style="clip-path:path('M0 30 C120 10 250 100 400 100 C560 100 620 0 760 10 C900 20 1000 -20 1200 0 L1200 622 L0 622Z')"></div>
<div class="abs about-photo" role="img" aria-label="Two women in a low lunge yoga pose with arms raised in a bright studio"></div>
<div class="abs about-mark"></div>
<h2 class="abs about-title script">About OpenHarbor Yoga</h2>
<div class="abs about-text">
  <p>My name is Hannah, and I am the creator &amp; facilitator of OpenHarbor Yoga. With the increasing numbers of youth mental health, I have started OpenHarbor Yoga wanting to assist children and teens with their mental health for life, with the magic of yoga.</p>
  <p>I had always wanted to teach children, but had never found the right platform to do so... That was until I found yoga!</p>
</div>
<div class="abs pill read-more">Read More</div>

<!-- benefits -->
<div class="abs benefits-mark"></div>
<h2 class="abs benefits-title script">Benefits of Yoga</h2>
<p class="abs benefits-intro">The benefits of yoga can last a lifetime. It is my aim &amp; passion to introduce yoga to kids of all ages and backgrounds so that they can not only experience the benefits of yoga but fall in love with the practice.Yoga benefits include:</p>

<div class="abs bodies">
  <h3 class="col-title">Healthy bodies</h3>
  <ul class="col-list">
    <li>• Develops strong, flexible and healthy bodies</li>
    <li>• Promotes spinal alignment and good posture</li>
    <li>• Builds energy and stamina</li>
    <li>• Improves internal physical function - organs, digestion, elimination, circulation, and blood flow.</li>
    <li>• Helps breathing and lung capacity......<b>Read More</b></li>
  </ul>
</div>

<svg class="abs" style="left:370px;top:1555px" width="460" height="460" viewBox="0 0 460 460">
  <circle cx="230" cy="231" r="223" fill="none" stroke="#5a2fc0" stroke-width="2"/>
</svg>
<div class="abs centre-mark" role="img" aria-label="Meditating figure yoga symbol"></div>
<div class="abs icon-disc" style="left:350px;top:1612px" role="img" aria-label="Healthy body icon"></div>
<div class="abs icon-disc" style="left:732px;top:1612px" role="img" aria-label="Healthy mind icon"></div>
<div class="abs icon-disc" style="left:541px;top:1957px" role="img" aria-label="Healthy spirit icon"></div>

<div class="abs minds">
  <h3 class="col-title">Healthy minds</h3>
  <ul class="col-list">
    <li>• Cultivates confidence and self-esteem</li>
    <li>• Develops concentration and attention</li>
    <li>• Clears the mind for better clarity and decision making</li>
    <li>• Helps relax and sleep better</li>
    <li>• Calms the nervous system</li>
    <li>• Learns to cope with stressful situations</li>
    <li>• Balances emotions.....<b>Read More</b></li>
  </ul>
</div>

<div class="abs spirits">
  <h3 class="col-title">Healthy spirits</h3>
  <p class="col-list">• Fosters creativity, expression and imagination• Cultivates kindness to themselves and others• Cultivates respect for self and others• Builds balance and inner quiet• Builds inner strength and resilience• Teaches self-awareness• Focuses on positive self-talk...<b>Read More</b></p>
</div>

<!-- footer -->
<div class="abs footer"></div>
<div class="abs foot-brand">OpenHarbor<br>Yoga</div>
<div class="abs social" style="left:112px;top:2605px" role="img" aria-label="Social profile"></div>
<div class="abs social" style="left:159px;top:2605px" role="img" aria-label="Social profile"></div>

<h4 class="abs foot-head script" style="left:430px;top:2418px">Quick Link</h4>
<ul class="abs foot-list" style="left:430px;top:2462px">
  <li><svg width="14" height="12"><path d="M0 6H11M6 1L12 6L6 11" fill="none" stroke="#fff" stroke-width="2.2"/></svg>Home</li>
  <li><svg width="14" height="12"><path d="M0 6H11M6 1L12 6L6 11" fill="none" stroke="#fff" stroke-width="2.2"/></svg>About</li>
  <li><svg width="14" height="12"><path d="M0 6H11M6 1L12 6L6 11" fill="none" stroke="#fff" stroke-width="2.2"/></svg>Classes</li>
  <li><svg width="14" height="12"><path d="M0 6H11M6 1L12 6L6 11" fill="none" stroke="#fff" stroke-width="2.2"/></svg>Blog</li>
  <li><svg width="14" height="12"><path d="M0 6H11M6 1L12 6L6 11" fill="none" stroke="#fff" stroke-width="2.2"/></svg>Contact</li>
</ul>

<h4 class="abs foot-head script" style="left:632px;top:2418px">Help Links</h4>
<ul class="abs foot-list" style="left:632px;top:2462px">
  <li><svg width="14" height="12"><path d="M0 6H11M6 1L12 6L6 11" fill="none" stroke="#fff" stroke-width="2.2"/></svg>FAQ</li>
  <li><svg width="14" height="12"><path d="M0 6H11M6 1L12 6L6 11" fill="none" stroke="#fff" stroke-width="2.2"/></svg>Terms of use</li>
  <li><svg width="14" height="12"><path d="M0 6H11M6 1L12 6L6 11" fill="none" stroke="#fff" stroke-width="2.2"/></svg>Privacy Policy</li>
  <li><svg width="14" height="12"><path d="M0 6H11M6 1L12 6L6 11" fill="none" stroke="#fff" stroke-width="2.2"/></svg>Enquire Now</li>
  <li><svg width="14" height="12"><path d="M0 6H11M6 1L12 6L6 11" fill="none" stroke="#fff" stroke-width="2.2"/></svg>More Information</li>
</ul>

<h4 class="abs foot-head script" style="left:858px;top:2418px">Contact Us</h4>
<div class="abs contact-row" style="left:858px;top:2475px">
  <span class="ico"><svg width="14" height="18" viewBox="0 0 14 18"><path d="M7 1C3.7 1 1 3.6 1 6.8 1 11 7 17 7 17S13 11 13 6.8C13 3.6 10.3 1 7 1Z" fill="#161616"/><circle cx="7" cy="6.8" r="2.2" fill="#fff"/></svg></span>
  <span>Fernvale, Victoria<br>Australia 3799</span>
</div>
<div class="abs contact-row" style="left:858px;top:2535px">
  <span class="ico"><svg width="16" height="16" viewBox="0 0 16 16"><path d="M3 1L6 4 4.5 6C5.5 8 8 10.5 10 11.5L12 10 15 13 13 15C7 15 1 9 1 3Z" fill="#161616"/></svg></span>
  <span>0400 555 018</span>
</div>
<div class="abs contact-row" style="left:858px;top:2587px">
  <span class="ico"><svg width="16" height="12" viewBox="0 0 16 12"><rect x="0" y="0" width="16" height="12" rx="2" fill="#161616"/><path d="M1 1L8 7 15 1" fill="none" stroke="#fff" stroke-width="1.5"/></svg></span>
  <span>info@openharboryoga.example</span>
</div>

<div class="abs copyright">Copyrights@2023.OpenHarbor Yoga.All Rights Reserved</div>

</body>
</html>
```